KVM Contracting services . Building and maintenance services, optic fibre installation

Business cards and logo design.I need a logo that I can use on business cards ,workwear and on my vehicles. I would like the KVM to be the main or larger text and contracting services to be the smaller or less important text.I like monograms, modern designs and repeating patterns symbols. I am also a Gemini and my favourite number is 22 so if this can be any inspiration to help with the design. Am thinking of the using German flag colours as a his is my family’s heritage. And the other 2 main colours I wear is black and white.But any ideas are appreciated.I do not need a design that is trade specific but a design that could be used for any business.

Target Market(s)

General public

Contact Information for Business Card

KVM Contracting Services ( front of business card)

(Back of business card)
Darren Holtwick
0451907326
Maintenance services
Optic fibre and data installation

Logo Text

Logo can just be pattern or monogram or incorporate KVM . I like the gemini star sign and the number 22

Colors
ec1f27
000000
fbee3e
ffffff

Requirements
Must have
• Logo and KVM Contracting Services on the front of business card
Nice to have
• Possible use of German flag colours.
• Modern design.
• Design to be able to be used on black or white background as I want to put it on clothing

```html
<!DOCTYPE html>
<html lang="en">
<head>
<meta charset="utf-8">
<title>KVM Contracting Services — Business Cards</title>
<link href="https://fonts.googleapis.com/css2?family=Jost:wght@600&family=Open+Sans:wght@400&display=swap" rel="stylesheet">
<style>
  :root {
    --stage: #2e2a28;
    --card-white: #f7f7f5;
    --ink: #1c1c1c;
    --ink-soft: #2a2a2a;
    --rule: #b9b9b9;
    --black: #000000;
    --deep-red: #5a0a0c;
    --red: #ec1f27;
    --orange: #f7781b;
    --yellow: #fbb21a;
    --white: #ffffff;
  }
  * { box-sizing: border-box; margin: 0; padding: 0; }
  html, body { width: 1200px; height: 844px; overflow: hidden; }
  body {
    background: var(--stage);
    display: flex;
    align-items: center;
    justify-content: center;
    gap: 48px;
    font-family: "Open Sans", Arial, sans-serif;
  }
  .card {
    position: relative;
    width: 520px;
    height: 300px;
    overflow: hidden;
    box-shadow: 0 14px 30px rgba(0,0,0,.45);
  }

  /* Back of card: contact details */
  .card--back { background: var(--card-white); }
  .card--back .accent-band {
    position: absolute;
    left: 0; right: 0; bottom: 0;
    height: 12px;
    background: linear-gradient(90deg, var(--yellow), var(--orange) 60%, var(--red));
  }
  .card--back .brand {
    position: absolute;
    right: 40px;
    top: 34px;
    text-align: right;
    color: var(--ink);
  }
  .brand-name {
    font-family: "Jost", Arial, sans-serif;
    font-weight: 600;
    line-height: 1;
    letter-spacing: 2px;
  }
  .brand-name .brand-initials { display: block; }
  .brand-name .brand-descriptor { display: block; letter-spacing: 1.5px; }
  .card--back .brand-initials { font-size: 64px; }
  .card--back .brand-descriptor { font-size: 17px; margin-top: 2px; }
  .card--back .divider {
    position: absolute;
    left: 40px; right: 40px;
    height: 1px;
    background: var(--rule);
  }
  .divider--top { top: 134px; }
  .contact {
    position: absolute;
    left: 40px;
    top: 158px;
    color: var(--ink);
  }
  .contact-name {
    font-family: "Jost", Arial, sans-serif;
    font-weight: 600;
    font-size: 19px;
    letter-spacing: 1px;
    text-transform: uppercase;
  }
  .contact-phone {
    font-size: 17px;
    letter-spacing: .5px;
    margin-top: 2px;
  }
  .divider--bottom { top: 222px; right: 260px; }
  .services {
    position: absolute;
    left: 40px;
    top: 230px;
    list-style: none;
    font-size: 14px;
    line-height: 1.35;
    color: var(--ink-soft);
  }

  /* Front of card: brand */
  .card--front {
    background: linear-gradient(160deg, var(--black) 0%, var(--deep-red) 22%, var(--red) 50%, var(--orange) 78%, var(--yellow) 100%);
  }
  .card--front .brand {
    position: absolute;
    inset: 0;
    display: flex;
    flex-direction: column;
    align-items: center;
    justify-content: center;
    color: var(--white);
    text-align: center;
  }
  .card--front .brand-initials { font-size: 88px; }
  .card--front .brand-descriptor { font-size: 22px; margin-top: 4px; }
</style>
</head>
<body>
  <section class="card card--back" aria-label="Business card back">
    <div class="brand">
      <p class="brand-name">
        <span class="brand-initials">KVM</span>
        <span class="brand-descriptor">CONTRACTING SERVICES</span>
      </p>
    </div>
    <div class="divider divider--top"></div>
    <div class="contact">
      <p class="contact-name">Darren Holtwick</p>
      <p class="contact-phone">0451907326</p>
    </div>
    <div class="divider divider--bottom"></div>
    <ul class="services">
      <li>Maintenance services</li>
      <li>Optic fibre and data installation</li>
    </ul>
    <div class="accent-band"></div>
  </section>

  <section class="card card--front" aria-label="Business card front">
    <div class="brand">
      <p class="brand-name">
        <span class="brand-initials">KVM</span>
        <span class="brand-descriptor">CONTRACTING SERVICES</span>
      </p>
    </div>
  </section>
</body>
</html>
```